Business Card Design

New business card design

Target Market(s)

Residential & Commercial Property Managers

Industry/Entity Type

Plumbing Services

Contact Information for Business Card

Name - Rowan Keddle, title - Director, Phone Number - 0431 286 517, email - rowan@tbk-plumbing.com.au, Company ABN - 73 215 904 386,

Font styles to use
Sans Serif

Colors
0054AA
0677BA
7BADD7
CADEEF
E8F1F8

```html
<!DOCTYPE html>
<html lang="en">
<head>
<meta charset="utf-8">
<title>TBK Plumbing Services – Business Card</title>
<link href="https://fonts.googleapis.com/css2?family=Montserrat:wght@400;500&family=Poppins:wght@700&family=Saira+Condensed:wght@400&display=swap" rel="stylesheet">
<style>
  :root {
    --canvas: #9a9a9a;
    --ink: #1e232a;
    --water: #00aeef;
    --royal: #0054aa;
    --paper: #ffffff;
    --muted: #8a8480;
  }
  * { box-sizing: border-box; margin: 0; padding: 0; }
  html, body { width: 1200px; height: 1108px; overflow: hidden; }
  body { background: var(--canvas); position: relative; font-family: "Montserrat", sans-serif; }

  .card { position: absolute; border-radius: 30px; overflow: hidden; }

  /* Back of card */
  .card--back {
    left: 243px; top: 122px; width: 723px; height: 414px;
    background: var(--ink);
    border-top: 3px solid var(--royal);
  }
  .card--back .wordmark {
    position: absolute; left: 0; right: 0; top: 108px;
    text-align: center; color: var(--paper);
    font-size: 104px; font-weight: 500; line-height: 1; letter-spacing: 6px;
  }
  .card--back .tagline {
    position: absolute; left: 0; right: 0; top: 255px;
    text-align: center; color: var(--paper);
  }

  .tagline {
    font-family: "Saira Condensed", sans-serif;
    font-size: 18px; letter-spacing: 14px; line-height: 1;
  }

  /* Front of card */
  .card--front {
    left: 243px; top: 580px; width: 713px; height: 418px;
    background: var(--paper);
  }
  .card--front .wordmark {
    position: absolute; left: 48px; top: 36px;
    color: var(--ink);
    font-size: 92px; font-weight: 500; line-height: 1; letter-spacing: 5px;
  }
  .card--front .tagline {
    position: absolute; left: 66px; top: 156px;
    color: var(--muted); font-size: 16px; letter-spacing: 13px;
  }

  .accent-circle {
    position: absolute; left: 556px; top: 112px;
    width: 270px; height: 270px; border-radius: 50%;
    background: var(--water);
  }

  .person { position: absolute; left: 46px; top: 236px; color: var(--ink); }
  .person__name { font-family: "Poppins", sans-serif; font-weight: 700; font-size: 28px; line-height: 1.2; }
  .person__title { font-size: 19px; margin-top: 2px; }

  .contact { position: absolute; left: 45px; top: 315px; list-style: none; color: var(--ink); font-size: 19px; }
  .contact li { display: flex; align-items: center; height: 26px; }
  .contact li + li { margin-top: 0; }
  .contact svg { width: 20px; height: 20px; margin-right: 14px; fill: var(--water); flex: none; }

  .footer-stripe {
    position: absolute; left: 0; top: 396px; width: 407px; height: 10px;
    background: var(--water);
  }
  .footer-band {
    position: absolute; left: 0; bottom: 0; width: 100%; height: 8px;
    background: var(--ink);
  }
  .footer-abn {
    position: absolute; right: 0; bottom: 0; width: 300px; height: 32px;
    background: var(--ink);
    clip-path: polygon(22px 0, 100% 0, 100% 100%, 0 100%);
  }
  .abn {
    position: absolute; left: 459px; top: 387px;
    color: var(--paper); font-size: 19px; letter-spacing: 0.3px;
  }
</style>
</head>
<body>

  <section class="card card--back" aria-label="Card back">
    <div class="wordmark">tbk</div>
    <div class="tagline">plumbing&nbsp;&nbsp;services</div>
  </section>

  <section class="card card--front" aria-label="Card front">
    <div class="accent-circle"></div>

    <div class="wordmark">tbk</div>
    <div class="tagline">plumbing&nbsp;&nbsp;services</div>

    <div class="person">
      <div class="person__name">Rowan Keddle</div>
      <div class="person__title">Director</div>
    </div>

    <ul class="contact">
      <li>
        <svg viewBox="0 0 24 24" aria-hidden="true"><path d="M6.6 10.8a15.1 15.1 0 0 0 6.6 6.6l2.2-2.2a1 1 0 0 1 1-.25 11.4 11.4 0 0 0 3.6.57 1 1 0 0 1 1 1V20a1 1 0 0 1-1 1A17 17 0 0 1 3 4a1 1 0 0 1 1-1h3.5a1 1 0 0 1 1 1c0 1.25.2 2.45.57 3.57a1 1 0 0 1-.25 1z"/></svg>
        0431 286 517
      </li>
      <li>
        <svg viewBox="0 0 24 24" aria-hidden="true"><path d="M2 5h20v14H2z" opacity="0"/><path d="M2 5h20l-10 7.5z"/><path d="M2 7.5l10 7.5 10-7.5V19H2z"/></svg>
        rowan@tbk-plumbing.com.au
      </li>
    </ul>

    <div class="footer-stripe"></div>
    <div class="footer-band"></div>
    <div class="footer-abn"></div>
    <div class="abn">ABN - 73 215 904 386</div>
  </section>

</body>
</html>
```